Looking to build a senior life alert web page

We definitely want to incorporate pictures of the product in which we're selling and want colors that resonate with the senior community. We're looking for something also clean and very easy to navigate. We're looking to pick a design immediately!
Based on something similar to that of our competition which can be located at the following
https://www.tovrelcarelink.example/
https://www.wellkestrix.example/

attached is the product we're selling

The name of our company is the golden harbor circle

Target Market(s)

Elderly people looking for a life alert device

Industry/Entity Type

Medical Equipment

Number of Pages Required

3 page

Font styles to use
Serif

Colors

Designer to choose colors to be used in the design.

Requirements
Must have
• Pictures of the product a nice UI experience that can be easily made mobile friendly
Nice to have
• Including area for video content maybe / friendly color LOGOS are attached for our company

```html
<!DOCTYPE html>
<html lang="en">
<head>
<meta charset="utf-8">
<title>Golden Harbor Circle</title>
<link rel="stylesheet" href="https://fonts.googleapis.com/css2?family=Open+Sans:wght@400;600;700&family=Roboto+Condensed:wght@400;700&display=swap">
<style>
:root{
  --blue:#2f9fd8;
  --navy:#1d4a7c;
  --orange:#e8891c;
  --ink:#222;
  --muted:#666;
  --pale:#eaf3fb;
  --grey:#efefef;
  --dark:#2a2a2a;
  --white:#fff;
}
*{box-sizing:border-box;margin:0;padding:0}
html,body{width:1200px;height:3502px;overflow:hidden}
body{font-family:"Open Sans",sans-serif;color:var(--ink);background:var(--white);position:relative}
.abs{position:absolute}
h2,h3,.cond{font-family:"Roboto Condensed",sans-serif;font-weight:400}
.btn{display:inline-block;background:var(--orange);color:#fff;border-radius:24px;font-size:13px;padding:10px 24px;text-transform:uppercase;text-decoration:none}
.body-text{font-size:14px;line-height:24px;color:var(--muted)}

.topbar{top:0;left:0;width:1200px;height:40px;background:var(--blue);color:#fff;font-size:12px}
.topbar .contact{left:86px;top:12px}
.topbar .contact span{margin-right:24px}
.topbar .links{left:780px;top:12px}
.topbar .links span{margin-right:14px}
.topbar .social{left:1060px;top:12px;display:flex;gap:6px}
.topbar .social i{display:block;width:14px;height:14px;background:#fff;border-radius:2px}

.header{top:40px;left:0;width:1200px;height:112px;background:#fff}
.brand{left:86px;top:32px;display:flex;align-items:center;gap:12px;font-weight:700;font-size:20px;color:var(--navy)}
.brand i{width:34px;height:34px;border-radius:50%;background:var(--orange);display:block}
.nav{left:408px;top:46px;display:flex;gap:52px;font-size:17px;color:#333}
.nav .on{color:var(--orange)}
.cart{left:1078px;top:40px;width:30px;height:30px;background:var(--orange);border-radius:3px}

.hero{top:152px;left:0;width:1200px;height:511px;background:linear-gradient(100deg,#6e7a4c 0%,#9aa068 35%,#b9b29a 60%,#6d6c5c 100%)}
.hero .device{left:86px;top:240px;width:101px;height:168px;background:linear-gradient(#f2f2f2,#cfcfcf);border-radius:12px}
.hero h1{left:217px;top:258px;font-family:"Roboto Condensed",sans-serif;font-weight:700;font-size:50px;line-height:60px;color:#fff;letter-spacing:1px;white-space:nowrap}
.hero p{left:219px;top:320px;font-family:"Roboto Condensed",sans-serif;font-size:28px;line-height:34px;color:#fff;white-space:nowrap}
.hero .arrows{left:1016px;top:430px;display:flex;gap:4px}
.hero .arrows span{width:22px;height:22px;border-radius:50%;background:#444;display:block}

.about{top:663px;left:0;width:1200px;height:448px;background:var(--pale)}
.about h2{left:100px;top:108px;font-size:32px;line-height:40px}
.about .body-text{left:100px;top:158px;width:484px;text-align:justify}
.about .btn{left:100px;top:300px}
.video{left:644px;top:77px;width:453px;height:296px;background:linear-gradient(120deg,#6f9a4a,#c9b9a4 50%,#7da1c0);box-shadow:0 4px 12px rgba(0,0,0,.2)}
.video .play{position:absolute;left:200px;top:122px}

.products{top:1111px;left:0;width:1200px;height:547px}
.products .shot{left:86px;top:79px;width:439px;height:362px;background:linear-gradient(135deg,#f4f4f4,#d6d6d6);border-radius:24px}
.products h2{left:560px;top:108px;font-size:32px;line-height:40px}
.products .body-text{left:560px;top:162px;width:540px;font-size:13px;line-height:20px}
.products ul{left:560px;top:232px;list-style:none;font-size:13px;line-height:26px;color:var(--muted)}
.products li::before{content:"» ";color:#333}
.products .btn{left:560px;top:386px}

.how{top:1658px;left:0;width:1200px;height:546px;background:linear-gradient(var(--navy),#1a4777)}
.how h2{left:0;top:86px;width:1200px;text-align:center;color:#fff;font-size:32px}
.step{top:192px;width:300px;text-align:center;color:#fff}
.step .ring{width:103px;height:103px;margin:0 auto;border:4px solid #c9d7e6;border-radius:50%;background:#fff;display:flex;align-items:center;justify-content:center}
.step h3{margin-top:36px;font-size:26px}
.step p{margin:10px auto 0;width:240px;font-size:13px;line-height:20px}
.step .more{margin-top:20px;font-style:italic;font-weight:600;font-size:15px}

.ourproduct{top:2204px;left:0;width:1200px;height:411px}
.ourproduct h2{left:163px;top:94px;font-size:32px;line-height:40px}
.ourproduct .body-text{left:163px;top:144px;width:502px;text-align:justify}
.ourproduct .btn{left:163px;top:290px}
.ourproduct .shot{left:743px;top:56px;width:354px;height:308px;background:linear-gradient(135deg,#e9e9e9,#f1c9a8);border-radius:28px}

.blog{top:2615px;left:0;width:1200px;height:420px;background:var(--grey)}
.blog h2{left:0;top:80px;width:1200px;text-align:center;font-size:32px}
.card{top:159px;width:497px;height:168px;background:#fff;box-shadow:0 2px 6px rgba(0,0,0,.15);display:flex}
.card .pic{width:161px;height:168px;flex:none}
.card .txt{padding:18px 24px;font-size:13px;line-height:19px;color:var(--muted)}
.card h3{font-size:17px;color:#444}
.card .date{margin:4px 0 6px}
.card .read{color:var(--navy);font-weight:600}

.footer{top:3035px;left:0;width:1200px;height:467px;background:var(--dark);color:#fff}
.footer .nl{left:262px;top:66px;font-family:"Roboto Condensed",sans-serif;font-size:30px}
.footer .email{left:467px;top:60px;width:350px;height:44px;background:#fff;border-radius:22px 0 0 22px;color:#999;font-size:12px;padding:14px 20px}
.footer .sub{left:817px;top:60px;width:93px;height:44px;background:var(--orange);border-radius:0 22px 22px 0;font-size:12px;text-align:center;line-height:44px}
.col{top:190px;font-size:12px;line-height:25px;color:#ddd}
.col h4{font-weight:400;font-size:15px;color:#fff;margin-bottom:10px;text-transform:uppercase}
.col li{list-style:none}
.col li::before{content:"» "}
.follow{display:flex;gap:12px;margin-top:16px}
.follow i{display:block;width:24px;height:24px;background:#fff;border-radius:3px}
.footer .rule{left:86px;top:343px;width:1028px;height:1px;background:#444}
.pay{left:472px;top:385px;display:flex;gap:8px}
.pay i{display:block;width:48px;height:30px;border-radius:3px}
.footer .copy{left:0;top:430px;width:1200px;text-align:center;font-size:12px}
</style>
</head>
<body>

<div class="abs topbar">
  <div class="abs contact"><span>☎ (555) 014 - 2290</span><span>✉ info@goldenharbor.example</span></div>
  <div class="abs links"><span>Register</span><span>|</span><span>Login</span><span style="margin-left:30px">My Account ▾</span></div>
  <div class="abs social"><i></i><i></i><i></i><i></i></div>
</div>

<header class="abs header">
  <div class="abs brand"><i></i>Golden Harbor Circle</div>
  <nav class="abs nav"><span class="on">Home</span><span>About us</span><span>Products</span><span>How it works</span><span>Blog</span><span>Contacts</span></nav>
  <div class="abs cart"></div>
</header>

<section class="abs hero" role="img" aria-label="Smiling senior woman jogging along a sunny park path">
  <div class="abs device" role="img" aria-label="Alert device product"></div>
  <h1 class="abs">GOLDEN HARBOR CIRCLE</h1>
  <p class="abs">Neque porro quisquam est dolorem</p>
  <div class="abs arrows"><span></span><span></span></div>
</section>

<section class="abs about">
  <h2 class="abs">About us</h2>
  <p class="abs body-text">It is a long established fact that a reader will be distracted by the readable content of a page when looking at its layout. The point of using Lorem Ipsum is that it has a more-or-less normal distribution of letters, as opposed to using 'Content here, content here', making it look like readable English. Many desktop publishing packages</p>
  <a class="abs btn">Read more »</a>
  <div class="abs video" role="img" aria-label="Video of a group of happy active seniors outdoors">
    <svg class="play" width="54" height="54" viewBox="0 0 54 54"><circle cx="27" cy="27" r="26" fill="rgba(40,40,40,.7)"/><path d="M21 16l18 11-18 11z" fill="#fff"/></svg>
  </div>
</section>

<section class="abs products">
  <div class="abs shot" role="img" aria-label="Two white emergency alert pendant devices"></div>
  <h2 class="abs">Golden Harbor Circle Products</h2>
  <p class="abs body-text">It is a long established fact that a reader will be distracted by the readable content of a page when looking at its layout. The point of using Lorem Ipsum is that it has a more-or-less normal distribution</p>
  <ul class="abs">
    <li>Neque porro quisquam est qui dolorem ipsum</li>
    <li>Porro quisquam est qui dolorem ipsum quia dolor sit amet,</li>
    <li>Quisquam est qui dolorem ipsum quia dolor sit amet</li>
    <li>Dolorem ipsum quia dolor sit amet, consectetur, adipisci velit</li>
    <li>Porro quisquam est qui dolorem ipsum quia dolor sit amet, consectetur</li>
  </ul>
  <a class="abs btn">Buy now »</a>
</section>

<section class="abs how" role="img" aria-label="Seniors cycling through a park, tinted blue">
  <h2 class="abs">How it works</h2>
  <div class="abs step" style="left:95px">
    <div class="ring"><svg width="40" height="40" viewBox="0 0 40 40"><rect x="10" y="4" width="20" height="32" rx="2" fill="none" stroke="var(--navy)" stroke-width="3"/></svg></div>
    <h3 class="cond">Step 1</h3>
    <p>It is a long established fact that a reader will be distracted by the readable content of a page</p>
    <div class="more">Learn More »</div>
  </div>
  <div class="abs step" style="left:445px">
    <div class="ring"><svg width="40" height="40" viewBox="0 0 40 40"><circle cx="20" cy="20" r="14" fill="none" stroke="var(--navy)" stroke-width="3"/><path d="M20 12v9h6" fill="none" stroke="var(--navy)" stroke-width="3"/></svg></div>
    <h3 class="cond">Step 2</h3>
    <p>It is a long established fact that a reader will be distracted by the readable content of a page</p>
    <div class="more">Learn More »</div>
  </div>
  <div class="abs step" style="left:805px">
    <div class="ring"><svg width="44" height="40" viewBox="0 0 44 40"><circle cx="22" cy="12" r="6" fill="var(--navy)"/><circle cx="9" cy="16" r="4.5" fill="var(--navy)"/><circle cx="35" cy="16" r="4.5" fill="var(--navy)"/><path d="M12 32a10 10 0 0 1 20 0z M1 32a8 8 0 0 1 13-6z M43 32a8 8 0 0 0-13-6z" fill="var(--navy)"/></svg></div>
    <h3 class="cond">Step 3</h3>
    <p>It is a long established fact that a reader will be distracted by the readable content of a page</p>
    <div class="more">Learn More »</div>
  </div>
</section>

<section class="abs ourproduct">
  <h2 class="abs">Our Product</h2>
  <p class="abs body-text">It is a long established fact that a reader will be distracted by the readable content of a page when looking at its layout. The point of using Lorem Ipsum is that it has a more-or-less normal distribution of letters, as opposed to using 'Content here, content here', making it look like readable English. Many desktop publishing packages</p>
  <a class="abs btn">Buy now</a>
  <div class="abs shot" role="img" aria-label="Hand holding the emergency alert device"></div>
</section>

<section class="abs blog">
  <h2 class="abs">Latest Blog</h2>
  <article class="abs card" style="left:86px">
    <div class="pic" role="img" aria-label="Senior woman on an exercise bike" style="background:linear-gradient(135deg,#cfd7dc,#6f8796)"></div>
    <div class="txt"><h3>Nemo Enim Ipsam Volup</h3><div class="date">09-07-2017</div><p>Lorem Ipsum has been the industry's standard dummy text ever since the 1500s, when an unknown printer took a galley</p><div class="read">Read More &gt;&gt;</div></div>
  </article>
  <article class="abs card" style="left:612px">
    <div class="pic" role="img" aria-label="Senior couple walking outdoors" style="background:linear-gradient(135deg,#a8b68c,#4f73a8)"></div>
    <div class="txt"><h3>Nemo Enim Ipsam Volup</h3><div class="date">09-07-2017</div><p>Lorem Ipsum has been the industry's standard dummy text ever since the 1500s, when an unknown printer took a galley</p><div class="read">Read More &gt;&gt;</div></div>
  </article>
</section>

<footer class="abs footer">
  <div class="abs nl">NEWSLETTER</div>
  <div class="abs email">email@example.com</div>
  <div class="abs sub">SUBSCRIBE</div>
  <div class="abs col" style="left:96px"><h4>Information</h4><ul><li>Privacy Policy</li><li>Your Account</li><li>Advanced Search</li><li>Cookies</li></ul></div>
  <div class="abs col" style="left:336px"><h4>Customer Service</h4><ul><li>Safe Shopping Guarantee</li><li>Shipping Rates</li><li>Returns</li><li>Return Policy</li></ul></div>
  <div class="abs col" style="left:623px;width:240px"><h4>Contact Us</h4><p>Address : 12 Harbor Lane, Maple Ridge, Westbury</p><p>Phone : 05550142298</p><p>Email : info@goldenharbor.example</p></div>
  <div class="abs col" style="left:936px"><h4>Follow us out there</h4><div class="follow"><i></i><i></i><i></i><i></i></div></div>
  <div class="abs rule"></div>
  <div class="abs pay"><i style="background:#3b6fb6"></i><i style="background:#7a2d6d"></i><i style="background:#1a3a8a"></i><i style="background:#e0e0e0"></i><i style="background:#f1f1f1"></i></div>
  <div class="abs copy">Copyright © 2017. All Rights Reserved</div>
</footer>

</body>
</html>
```